Friendly website/webshop needed for small family store

Hello .. I really need a website that is easy to use as I have no experience with this at all. ..
My shop is called quillmoss and I had a fantastic logo from craft forge - I asked for something mid century modern and I love it. I will attach . There might be some development around the logo now for various paraphernalia ( stickers , printed tissue paper carrier bags etc.. ) I would also like some sort of help with a slogan such as 'sing your prettiest song' as in,  live your best life etc..  but I'm not sure if this is a little trite .... ? but it would be nice to link the quillmoss with a little Motto.    If I need to pay extra for this - please could you let me know ... I'm happy to add on payment ..
As you can see the only LOGO colours really are grey black and orange .. so I would like some ideas to expand on the bird  to bring in some more colours.....  the tag line flower.children.home I would like to drop..
* the original brief included flowers on the tag line  because at the time we were also a florist . we now just sell dried flowers
My shop is in the beautiful town of Malvern, we have lots of tourist that come to walk the hills and enjoy nature - it's a family and dog friendly sort of town and we are a dog and family friendly sort of shop :-) It's a relaxed space that focuses on beautiful handmade items such as baskets & wooden utensils  from Africa, textiles from India and ceramics from France, Portugal and Italy.  We have a lovely section for children that sells beautiful soft toys from Charmel Duvo and the wonderful mice family and bunnies from Tornby.
We stock OBRETI homeware which is lovely and earthy and natural.
We would like to communicate the value of buying thoughtfully  and conscientiously, of building a beautiful home whilst investing in & supporting makers world wide. We don't sell anything that can't be repurposed, recycled etc..
Thank you

```html
<!DOCTYPE html>
<html lang="en">
<head>
<meta charset="utf-8">
<title>quillmoss</title>
<link href="https://fonts.googleapis.com/css2?family=Righteous&family=Poppins:wght@400;500;600&display=swap" rel="stylesheet">
<style>
:root{
  --sky:#79b4c4;
  --sky-dark:#5f9fb0;
  --clay:#d4867a;
  --clay-bg:#d98d80;
  --slate:#6b6e7a;
  --ink:#1f1f1f;
  --panel:#f3f3f3;
  --white:#ffffff;
  --sale:#ef5b5b;
  --star:#f4b400;
}
*{margin:0;padding:0;box-sizing:border-box}
html,body{width:1200px;height:4032px;overflow:hidden}
body{position:relative;font-family:"Poppins",sans-serif;color:var(--ink);background:var(--white)}
.abs{position:absolute}

/* top bar */
.topbar{left:0;top:0;width:1200px;height:70px;background:var(--sky)}
.contact-item{top:22px;color:var(--white);font-size:14px;display:flex;align-items:center;gap:10px}
.social{display:flex;gap:6px}
.social span{display:block;width:26px;height:26px;border-radius:50%;background:var(--white)}
.topbar .social{position:absolute;left:928px;top:22px}
.brand-badge{left:524px;top:-82px;width:152px;height:152px;border-radius:50%;background:var(--white);z-index:2}
.nav{left:0;top:70px;width:1200px;height:60px;background:var(--white);box-shadow:0 1px 3px rgba(0,0,0,.08);z-index:3}
.nav a{position:absolute;top:21px;font-size:15px;color:var(--ink);text-decoration:none}
.brand-name{font-family:"Poppins",sans-serif;font-weight:600;font-size:24px;color:var(--slate);letter-spacing:.3px}
.nav .brand-name{position:absolute;left:0;top:8px;width:1200px;text-align:center}

/* hero */
.hero{left:0;top:130px;width:1200px;height:643px;background:var(--sky)}
.hero-photo{left:440px;top:0;width:760px;height:643px;background:linear-gradient(90deg,rgba(121,180,196,1) 0%,rgba(150,170,180,.85) 35%,#a2a6ad 65%,#8a8580 100%)}
.hero h1{left:110px;top:175px;font-family:"Righteous",sans-serif;font-weight:400;font-size:50px;line-height:52px;color:var(--white);text-shadow:2px 2px 0 rgba(0,0,0,.25)}
.hero p{left:110px;top:298px;width:420px;font-size:16px;line-height:31px;color:var(--white)}
.btn{display:flex;align-items:center;justify-content:center;font-weight:600;text-transform:uppercase;border-radius:6px 0 6px 0;box-shadow:3px 3px 0 rgba(0,0,0,.18)}
.hero .btn{left:110px;top:418px;width:159px;height:44px;background:var(--white);font-size:15px}

/* about */
.about-photo{left:132px;top:884px;width:394px;height:380px;border-radius:50% 46% 52% 48%/52% 50% 50% 48%;background:linear-gradient(135deg,#c7c2bb,#6f7d93 55%,#d6a58f)}
.about-ring{left:116px;top:856px}
.about h2{left:599px;top:870px;font-family:"Righteous",sans-serif;font-weight:400;font-size:31px;color:var(--clay)}
.about p{left:599px;top:926px;width:490px;font-size:15.5px;line-height:30.8px;color:var(--ink)}
.about .btn{left:599px;top:1197px;width:160px;height:44px;background:var(--clay);color:var(--white);font-size:15px}

/* products */
.products{left:0;top:1341px;width:1200px;height:718px;background:var(--clay-bg)}
.products h2,.best h2,.contact h2{width:100%;text-align:center;font-family:"Righteous",sans-serif;font-weight:400;font-size:31px}
.products h2{top:76px;color:var(--white)}
.products .lead{left:80px;top:132px;width:1040px;text-align:center;font-size:15.5px;line-height:31px;color:var(--white)}
.product{width:240px;text-align:center;top:230px}
.product .thumb{width:204px;height:204px;border-radius:50%;margin:0 auto;border:3px solid var(--white)}
.product h3{font-family:"Poppins",sans-serif;font-weight:400;font-size:20px;color:var(--white);margin-top:20px}
.price{font-size:19px;color:var(--ink);margin-top:4px}
.price s{font-size:14px;color:#7a4a42}
.pill{display:inline-block;background:var(--white);border-radius:14px;font-size:11px;font-weight:600;padding:7px 22px;margin-top:10px}
.view-all{width:160px;height:45px;background:var(--white);font-size:16px}
.products .view-all{left:521px;top:604px}

/* best selling */
.best{left:111px;top:2143px;width:978px;height:751px;background:var(--panel)}
.best h2{top:56px;color:var(--clay)}
.best .lead{left:80px;top:124px;width:818px;text-align:center;font-size:15.5px;line-height:27px}
.card{top:221px;width:221px;height:360px;background:var(--white);text-align:center}
.sale{position:absolute;right:10px;top:10px;width:40px;height:40px;border-radius:50%;background:var(--sale);color:var(--white);font-size:11px;display:flex;align-items:center;justify-content:center}
.card .thumb{width:150px;height:150px;margin:50px auto 0;border-radius:8px}
.card h4{font-weight:500;font-size:17px;line-height:20px;margin-top:18px}
.card .cost{font-size:13px;margin-top:6px}
.card .cost span{color:var(--sky-dark)}
.stars{color:var(--star);font-size:11px;letter-spacing:2px;margin-top:4px}
.cart{display:inline-block;background:var(--sky);color:var(--white);font-size:11px;padding:5px 13px;border-radius:12px;margin-top:6px}
.best .view-all{left:410px;top:639px}

/* contact */
.contact{left:111px;top:2894px;width:978px;height:698px;background:linear-gradient(160deg,#868b9c,#6f758c 60%,#7d8295)}
.contact h2{top:66px;color:var(--white)}
.contact .lead{left:80px;top:118px;width:818px;text-align:center;font-size:15.5px;line-height:26px;color:var(--white)}
.field{background:var(--white);border-radius:0 0 12px 0;font-size:13px;color:#333;padding:13px 16px}
.send{left:246px;top:587px;width:206px;height:42px;border:2px solid var(--white);color:var(--white);border-radius:10px 0 10px 0;font-size:15px;font-weight:500;letter-spacing:1.5px;display:flex;align-items:center;justify-content:center}

/* footer */
.footer{left:0;top:3675px;width:1200px;height:357px;background:var(--sky);color:var(--white)}
.footer-brand{left:110px;top:148px;width:190px;text-align:center}
.footer .social{position:absolute;left:110px;top:232px;gap:13px}
.col{top:82px}
.col h5{font-family:"Righteous",sans-serif;font-weight:400;font-size:23px;margin-bottom:14px}
.col li{list-style:none;font-size:15px;line-height:30.7px}
.rule{left:111px;top:294px;width:975px;height:1px;background:var(--white)}
.copy{left:0;top:312px;width:1200px;text-align:center;font-size:16px}
</style>
</head>
<body>

<header>
  <div class="abs topbar">
    <div class="abs contact-item" style="left:110px">
      <svg width="20" height="20" viewBox="0 0 24 24" fill="none" stroke="#fff" stroke-width="1.6"><path d="M5 3h4l2 5-3 2a11 11 0 0 0 6 6l2-3 5 2v4a2 2 0 0 1-2 2A17 17 0 0 1 3 5a2 2 0 0 1 2-2z"/></svg>
      (+1) 555 0142 0199
    </div>
    <div class="abs contact-item" style="left:316px">
      <svg width="20" height="20" viewBox="0 0 24 24" fill="none" stroke="#fff" stroke-width="1.6"><rect x="3" y="5" width="18" height="14" rx="2"/><path d="M3 7l9 6 9-6"/></svg>
      hello@quillmoss.shop
    </div>
    <div class="social" aria-label="Social links"><span></span><span></span><span></span><span></span><span></span></div>
  </div>
  <div class="abs brand-badge"></div>
  <nav class="abs nav">
    <a style="left:110px">Home</a>
    <a style="left:206px">About Us</a>
    <a style="left:331px">Our Products</a>
    <a style="left:774px">Our Services</a>
    <a style="left:918px">Blog</a>
    <a style="left:1003px">Contact Us</a>
    <div class="brand-name">quillmoss</div>
  </nav>
</header>

<section class="abs hero">
  <div class="abs hero-photo" role="img" aria-label="Shop interior with shelves of baskets, dried flowers and homeware"></div>
  <h1 class="abs">Welcome To<br>Quillmoss</h1>
  <p class="abs">Lorem ipsum dolor sit amet, consectetur adipiscing elit, sed do eiusmod tempor incididunt ut labore et dolore magna aliqua. Ut enim ad minim veniam,</p>
  <div class="abs btn">Get Started</div>
</section>

<section class="about">
  <svg class="abs about-ring" width="420" height="420" viewBox="0 0 420 420"><path d="M150 20 A196 196 0 0 1 410 190" fill="none" stroke="#333" stroke-width="2" stroke-dasharray="8 7"/><path d="M10 210 A196 196 0 0 0 100 380" fill="none" stroke="#333" stroke-width="2" stroke-dasharray="8 7"/></svg>
  <div class="abs about-photo" role="img" aria-label="A family shopping together with a basket"></div>
  <h2 class="abs">ABOUT US</h2>
  <p class="abs">Lorem ipsum dolor sit amet, consectetur adipiscing elit, sed do eiusmod tempor incididunt ut labore et dolore magna aliqua. Ut enim ad minim veniam, quis nostrud exercitation ullamco laboris nisi ut aliquip ex ea commodo consequat. Duis aute irure dolor in reprehenderit in voluptate velit esse cillum dolore eu fugiat nulla pariatur. Excepteur sint occaecat cupidatat non proident, sunt in culpa qui officia deserunt mollit anim id est laborum.</p>
  <div class="abs btn">Get Started</div>
</section>

<section class="abs products" role="img" aria-label="Warm blush backdrop of soft toys and macarons">
  <h2 class="abs">OUR PRODUCTS</h2>
  <p class="abs lead">Lorem ipsum dolor sit amet, consectetur adipiscing elit, sed do eiusmod tempor incididunt ut labore et dolore magna aliqua. Ut enim ad minim veniam, quis nostrud exercitation ullamco laboris nisi ut aliquip ex ea commodo consequat.</p>
  <div class="abs product" style="left:126px">
    <div class="thumb" role="img" aria-label="Wicker picnic basket" style="background:radial-gradient(circle,#b87440 30%,#f3eeea 70%)"></div>
    <h3>Baskets</h3>
    <div class="price">$ 13.00 <s>&amp; 36.00</s></div>
    <div class="pill">ORDER NOW</div>
  </div>
  <div class="abs product" style="left:481px">
    <div class="thumb" role="img" aria-label="Heap of colourful textiles" style="background:radial-gradient(circle,#7a6a5a 20%,#3c3f4a 60%,#6f7f8a)"></div>
    <h3>Textiles</h3>
    <div class="price">$ 16.00 <s>&amp; 36.00</s></div>
    <div class="pill">ORDER NOW</div>
  </div>
  <div class="abs product" style="left:842px">
    <div class="thumb" role="img" aria-label="Two stacked ceramic cups" style="background:radial-gradient(circle,#2e2c2a 22%,#ededec 50%)"></div>
    <h3>ceramics</h3>
    <div class="price">$ 18.00 <s>&amp; 36.00</s></div>
    <div class="pill">ORDER NOW</div>
  </div>
  <div class="abs btn view-all">View All</div>
</section>

<section class="abs best">
  <h2 class="abs">BEST SELLING PRODUCTS</h2>
  <p class="abs lead">Lorem ipsum dolor sit amet, consectetur adipiscing elit, sed do eiusmod tempor incididunt ut labore et dolore magna aliqua. Ut enim ad minim veniam.</p>
  <div class="abs card" style="left:22px"><div class="sale">Sale!</div><div class="thumb" role="img" aria-label="Wicker basket with handle" style="background:radial-gradient(circle,#b8773f 35%,#fff 70%)"></div><h4>Lorem ipsum dolor<br>sit amet</h4><div class="cost">$ 65.00 <span>$ 60.00</span></div><div class="stars">★★★★★</div><div class="cart">Add to cart</div></div>
  <div class="abs card" style="left:258px"><div class="sale">Sale!</div><div class="thumb" role="img" aria-label="Wooden spoon" style="background:radial-gradient(ellipse,#b97a45 25%,#fff 60%)"></div><h4>Lorem ipsum dolor<br>sit amet</h4><div class="cost">$ 65.00 <span>$ 60.00</span></div><div class="stars">★★★★★</div><div class="cart">Add to cart</div></div>
  <div class="abs card" style="left:495px"><div class="sale">Sale!</div><div class="thumb" role="img" aria-label="Cream ceramic plate" style="background:radial-gradient(circle,#ece4d2 35%,#fff 65%)"></div><h4>Lorem ipsum dolor<br>sit amet</h4><div class="cost">$ 65.00 <span>$ 60.00</span></div><div class="stars">★★★★★</div><div class="cart">Add to cart</div></div>
  <div class="abs card" style="left:731px"><div class="sale">Sale!</div><div class="thumb" role="img" aria-label="Low woven basket" style="background:radial-gradient(ellipse,#c9915e 30%,#fff 62%)"></div><h4>Lorem ipsum dolor<br>sit amet</h4><div class="cost">$ 65.00 <span>$ 60.00</span></div><div class="stars">★★★★★</div><div class="cart">Add to cart</div></div>
  <div class="abs btn view-all">View All</div>
</section>

<section class="abs contact" role="img" aria-label="Muted backdrop of macarons and knitted wool">
  <h2 class="abs">CONTACT US</h2>
  <p class="abs lead">Lorem ipsum dolor sit amet, consectetur adipiscing elit, sed do eiusmod tempor incididunt ut labore et dolore magna aliqua. Ut enim ad minim veniam.</p>
  <div class="abs field" style="left:246px;top:222px;width:206px;height:43px">First Name</div>
  <div class="abs field" style="left:526px;top:222px;width:208px;height:43px">Last Name</div>
  <div class="abs field" style="left:246px;top:291px;width:488px;height:43px">Phone Number</div>
  <div class="abs field" style="left:246px;top:360px;width:488px;height:42px">E -mail</div>
  <div class="abs field" style="left:246px;top:429px;width:488px;height:131px">Message</div>
  <div class="abs send">SEND MESSAGE</div>
</section>

<footer class="abs footer">
  <div class="abs footer-brand brand-name">quillmoss</div>
  <div class="social" aria-label="Social links"><span></span><span></span><span></span><span></span><span></span></div>
  <div class="abs col" style="left:454px"><h5>OUR SERVICES</h5><ul><li>Baskets</li><li>Wooden utensils</li><li>Textiles</li><li>Ceramics</li><li>Soft toys</li></ul></div>
  <div class="abs col" style="left:684px"><h5>ABOUT</h5><ul><li>Home</li><li>About Us</li><li>Our Products</li><li>Our Blog</li><li>Contact</li></ul></div>
  <div class="abs col" style="left:903px"><h5>QUICK LINKS</h5><ul><li>Privacy Policy</li><li>Terms of Use</li><li>Site Map</li><li>Support</li></ul></div>
  <div class="abs rule"></div>
  <div class="abs copy">© Copyrights 2024 Quillmoss. - All rights reserved.</div>
</footer>

</body>
</html>
```